International emerging specialist Research and Development Company focused on plant-based medicine

We need a powerpoint design for a new company based in British Columbia, Canada called Tavrel Phytocor. We are focused on developing plant-based medicines. The company is driven by its experience in research and development work in plant genetics, cultivation techniques, natural medicines, biochemistry, agriculture and technologies. Tavrel will research, develop and produce very unique and specific cultivars from the plant kingdom needed for specific ailments in medical patients. We would like to see designs that use our current logo and its colour scheme. The final design should communicate financial safety, growth, and research and development.

```html
<!DOCTYPE html>
<html lang="en">
<head>
<meta charset="utf-8">
<title>Tavrel Phytocor – Thanks for your Time</title>
<link rel="stylesheet" href="https://fonts.googleapis.com/css2?family=Roboto+Condensed:wght@400&family=Source+Sans+3:wght@400;600&display=swap">
<style>
  :root {
    --brand-red: #d0070f;
    --panel-white: #ffffff;
    --text-grey: #5a5a5a;
    --icon-grey: #5f5f5f;
    --on-red: #ffffff;
  }
  html, body {
    margin: 0;
    padding: 0;
    overflow: hidden;
    background: var(--brand-red);
  }
  .slide {
    position: relative;
    width: 1200px;
    height: 900px;
    background: var(--brand-red);
    overflow: hidden;
    font-family: "Source Sans 3", "Myriad Pro", sans-serif;
  }
  .brand-name {
    position: absolute;
    left: 120px;
    top: 476px;
    margin: 0;
    display: flex;
    align-items: center;
    gap: 18px;
    color: var(--on-red);
    font-family: "Source Sans 3", sans-serif;
    font-weight: 400;
    font-size: 54px;
    line-height: 1;
    letter-spacing: 0.5px;
    white-space: nowrap;
  }
  .brand-dot {
    width: 22px;
    height: 22px;
    border-radius: 50%;
    background: var(--on-red);
    flex: none;
  }
  .closing-title {
    position: absolute;
    left: 644px;
    top: 254px;
    margin: 0;
    color: var(--on-red);
    font-family: "Roboto Condensed", "Arial Narrow", sans-serif;
    font-weight: 400;
    font-size: 52px;
    line-height: 1.1;
    white-space: nowrap;
  }
  .contact-panel {
    position: absolute;
    left: 642px;
    top: 358px;
    width: 558px;
    height: 326px;
    background: var(--panel-white);
    color: var(--text-grey);
    box-sizing: border-box;
    padding: 24px 0 0 33px;
  }
  .contact-intro {
    margin: 0;
    font-size: 28px;
    line-height: 38px;
  }
  .contact-list {
    list-style: none;
    margin: 40px 0 0;
    padding: 0;
    font-size: 28px;
    line-height: 37.5px;
  }
  .contact-item {
    display: flex;
    align-items: center;
    white-space: nowrap;
  }
  .contact-icon {
    width: 32px;
    height: 24px;
    margin-left: 2px;
    fill: var(--icon-grey);
    flex: none;
  }
  .contact-sep {
    width: 38px;
    text-align: center;
    margin-left: 4px;
  }
  .contact-value {
    margin-left: 10px;
  }
</style>
</head>
<body>
  <main class="slide">
    <p class="brand-name"><span class="brand-dot"></span>Tavrel Phytocor</p>

    <h1 class="closing-title">Thanks for your Time</h1>

    <section class="contact-panel">
      <p class="contact-intro">Lorem ipsum dolor sit amet,<br>consectetur adipiscing elit.<br>Donec accumsan.</p>
      <ul class="contact-list">
        <li class="contact-item">
          <svg class="contact-icon" viewBox="0 0 32 24" aria-hidden="true">
            <path d="M9 3c1.5-1 3-1 3.5.5l1.2 3.2c.3.9 0 1.6-.8 2.1l-1.3.8c.6 2.6 2.1 5 4.2 6.6l1.2-.9c.8-.5 1.6-.4 2.2.3l2 2.6c.8 1.1.3 2.3-1 3-2.4 1.3-5.2.6-7.6-1.8C9.5 16.3 8 12.3 7.7 8.6 7.5 6 7.9 3.9 9 3z"/>
          </svg>
          <span class="contact-sep">:</span>
          <span class="contact-value">604 555 0187</span>
        </li>
        <li class="contact-item">
          <svg class="contact-icon" viewBox="0 0 32 24" aria-hidden="true">
            <path d="M2 5h28v14H2z"/>
            <path d="M2 5l14 9 14-9" fill="none" stroke="#ffffff" stroke-width="1.6"/>
            <path d="M2 19l10-7M30 19l-10-7" fill="none" stroke="#ffffff" stroke-width="1.2"/>
          </svg>
          <span class="contact-sep">:</span>
          <span class="contact-value">hello@tavrel.ca</span>
        </li>
        <li class="contact-item">
          <svg class="contact-icon" viewBox="0 0 32 24" aria-hidden="true">
            <path d="M25 2L4 11l8 2.5L14.5 22z"/>
          </svg>
          <span class="contact-sep">:</span>
          <span class="contact-value">www.tavrel.ca</span>
        </li>
      </ul>
    </section>
  </main>
</body>
</html>
```